tinyTally Resource Book - 10 maths tasks to do outside

I need a 22 (11 pages back to back) page A6 sized book produced to standard for submission to professional printer. Needs to be as .pdf file showing guide lines and allowances for colour bleed. I have text already written and submitted as attachment in a Word file with margins set to A6 size. The theme of the materials is "Nature Play" so using lots of pictures from nature (Australia preferably) and showing lots of patterns in nature (rocks, leaves, flower petals etc). Some of the tasks refer to specific activities, such as "shadows" and "floating" so would be great to illustrate appropriately. The big emphasis is on learning outside the classroom, getting kids to engage actively with nature. I would like to see the pages as full colour - so not white background. The book itself will be spiral bound along the top edge so a margin of at least 1cm will be required at the top of each page (or the bottom of even numbered pages). Book will be printed on plastic laminated matte paper for outdoor use. Font size needs to be big enough to read. Fonts sizes, alignments and page numbers are all different at the moment and need to be standardised. One photo is included in a page as a sample if you can use it, otherwise disregard. Logo for Wattlebrook Numeracy Guild is also included to have as part of the acknowledgements at the back of the book.

Target Market(s)

Book is for early childhood and preschool teachers.

Industry/Entity Type

Education

Font styles to use
Sans Serif

Requirements
Must have
• Colour and appeal.
Nice to have
• Use of natural colours instead of bright catchy colours but that is your call.
Should not have
• American spelling

```html
<!DOCTYPE html>
<html lang="en-AU">
<head>
<meta charset="utf-8">
<title>How Many Leaves? – tinyTally Task Card</title>
<link rel="stylesheet" href="https://fonts.googleapis.com/css2?family=Jost:ital,wght@0,400;0,600;0,700;1,700&display=swap">
<style>
  :root {
    --paper: #ffffff;
    --mist-light: #e6efe9;
    --mist-mid: #c9d9d2;
    --mist-dark: #aebfba;
    --leaf-rose: #c9577f;
    --ink-blue: #1e2fe0;
    --ink-body: #2a2a2a;
    --bullet-red: #e0102a;
    --trim: #222222;
  }
  html, body {
    margin: 0;
    width: 892px;
    height: 1200px;
    overflow: hidden;
    background: var(--paper);
    font-family: "Jost", "Futura", sans-serif;
  }
  .canvas { position: relative; width: 892px; height: 1200px; }
  .trim-marks { position: absolute; inset: 0; }
  .page {
    position: absolute;
    left: 54px; top: 54px; width: 784px; height: 1092px;
    overflow: hidden;
  }
  .page-backdrop {
    position: absolute; inset: 0;
    background:
      radial-gradient(ellipse 45% 30% at 45% 75%, rgba(201,87,127,0.45), transparent 70%),
      radial-gradient(ellipse 30% 20% at 55% 45%, rgba(201,87,127,0.25), transparent 70%),
      radial-gradient(ellipse 60% 40% at 30% 30%, var(--mist-light), transparent 80%),
      linear-gradient(160deg, var(--mist-light) 0%, var(--mist-mid) 55%, var(--mist-dark) 100%);
  }
  .line { position: absolute; white-space: nowrap; line-height: 1; }
  .title, .outcome {
    left: 0; right: 0; text-align: center;
    color: var(--ink-blue); font-weight: 700;
    -webkit-text-stroke: 0;
    text-shadow:
      2px 0 0 #fff, -2px 0 0 #fff, 0 2px 0 #fff, 0 -2px 0 #fff,
      2px 2px 0 #fff, -2px -2px 0 #fff, 2px -2px 0 #fff, -2px 2px 0 #fff,
      3px 4px 4px rgba(0,0,0,0.35);
  }
  .title { font-size: 51px; letter-spacing: 0.3px; }
  .outcome { font-size: 32px; font-weight: 600; }
  .prompt {
    left: 70px; font-size: 25px; font-weight: 700; font-style: italic;
    color: var(--ink-blue);
  }
  .body-text { left: 142px; font-size: 32px; color: var(--ink-body); }
  .aim { left: 164px; font-size: 30px; color: var(--ink-body); }
  .aim.continued { left: 164px; }
  .aim-text { padding-left: 33px; }
  .aim-marker {
    position: absolute; left: 2px; top: 7px; width: 16px; height: 16px;
    background: var(--bullet-red); transform: rotate(45deg);
  }
</style>
</head>
<body>
<div class="canvas">
  <svg class="trim-marks" width="892" height="1200" viewBox="0 0 892 1200" aria-hidden="true">
    <g stroke="var(--trim)" stroke-width="1" fill="none">
      <path d="M54 0 V40 M0 54 H40 M74 36 V74 H36"/>
      <path d="M838 0 V40 M892 54 H852 M818 36 V74 H856"/>
      <path d="M54 1200 V1160 M0 1146 H40 M74 1164 V1126 H36"/>
      <path d="M838 1200 V1160 M892 1146 H852 M818 1164 V1126 H856"/>
    </g>
  </svg>

  <section class="page">
    <div class="page-backdrop" role="img" aria-label="Soft-focus background of autumn maple leaves in rose, orange and green over a misty pale green sky"></div>

    <h1 class="line title" style="top:84px;margin:0;">1. How Many Leaves?</h1>
    <div class="line outcome" style="top:163px;">EYLF – Outcome 1:</div>
    <div class="line outcome" style="top:207px;">Children have a strong sense</div>
    <div class="line outcome" style="top:249px;">of identity</div>

    <div class="line prompt" style="top:312px;">Children learn to interact in relation to others</div>
    <div class="line prompt" style="top:349px;">with care, empathy and respect when they...</div>
    <div class="line body-text" style="top:387px;">display awareness of and respect for</div>
    <div class="line body-text" style="top:433px;">others’ perspectives</div>

    <div class="line prompt" style="top:483px;">Educators promote this learning when</div>
    <div class="line prompt" style="top:519px;">they...</div>
    <div class="line body-text" style="top:555px;">organise learning environments</div>
    <div class="line body-text" style="top:599px;">in ways that promote small group</div>
    <div class="line body-text" style="top:641px;">interactions and play experiences</div>

    <div class="line prompt" style="top:689px;">This task provides an opportunity to:</div>
    <div class="line aim" style="top:728px;"><span class="aim-marker"></span><span class="aim-text">explore the concepts of “perspective”</span></div>
    <div class="line aim continued" style="top:770px;"><span class="aim-text">and “comparing”</span></div>
    <div class="line aim" style="top:812px;"><span class="aim-marker"></span><span class="aim-text">attempt the same task in different</span></div>
    <div class="line aim continued" style="top:855px;"><span class="aim-text">ways</span></div>
    <div class="line aim" style="top:897px;"><span class="aim-marker"></span><span class="aim-text">consider relationship between the</span></div>
    <div class="line aim continued" style="top:939px;"><span class="aim-text">individual and the group</span></div>
  </section>
</div>
</body>
</html>
```